Looking for a cool & simple business-card-design for digital agency

Hi!

We are a web agency that offers Reputation Management, Vextor & Seo Services and software development. We like cool things, we like innovative styles.

We have uploaded our logo.

Project Deadline Extended Reason: Client does not want any designs with the colorful logo. Please send us submissions ONLY with the blac and white logo. What the client would like to see:1) Back of the card: is a silver logo on a black background2) front of the card with all the data, please use white background and black logo thank you Added Friday, May 8, 2015

Industry/Entity Type

Software

```html
<!DOCTYPE html>
<html lang="en">
<head>
<meta charset="utf-8">
<title>Nordwell AG Business Card</title>
<link href="https://fonts.googleapis.com/css2?family=Source+Sans+3:ital,wght@0,400;0,600;0,700;1,700&display=swap" rel="stylesheet">
<style>
  :root {
    --stage: #8a8a8a;
    --card-white: #ffffff;
    --card-black: #231f20;
    --ink: #231f20;
    --ink-muted: #8c8c8c;
    --silver: #f2f2f2;
  }
  * { margin: 0; padding: 0; box-sizing: border-box; }
  html, body { width: 1200px; height: 907px; overflow: hidden; }
  body {
    background: var(--stage);
    font-family: "Source Sans 3", sans-serif;
    position: relative;
  }
  .card {
    position: absolute;
    left: 300px;
    width: 601px;
    height: 343px;
    box-shadow: 2px 3px 6px rgba(0,0,0,0.35);
  }
  .card-front { top: 91px; background: var(--card-white); color: var(--ink); }
  .card-back { top: 472px; background: var(--card-black); color: var(--silver); }

  .brand {
    position: absolute;
    left: 26px;
    top: 44px;
    display: flex;
    align-items: center;
    gap: 12px;
  }
  .brand-mark {
    width: 30px; height: 30px;
    border-radius: 50%;
    background: var(--ink);
  }
  .brand-divider {
    width: 1.5px; height: 44px;
    background: var(--ink);
  }
  .brand-name {
    font-size: 34px;
    font-weight: 700;
    line-height: 1;
    letter-spacing: 0.5px;
  }
  .brand-tagline {
    font-size: 15px;
    font-weight: 400;
    letter-spacing: 4.5px;
    margin-top: 4px;
  }

  .person {
    position: absolute;
    left: 106px;
    top: 113px;
  }
  .person-name { font-size: 22px; font-weight: 600; line-height: 1.1; }
  .person-title { font-size: 17px; font-weight: 600; color: var(--ink-muted); margin-top: 3px; }
  .address { font-size: 14px; line-height: 19px; margin-top: 13px; }
  .contacts { list-style: none; margin-top: 8px; font-size: 14px; }
  .contacts li { display: flex; align-items: center; height: 22px; }
  .contacts svg { width: 14px; height: 14px; margin-right: 10px; fill: var(--ink); }

  .back-brand {
    position: absolute;
    left: 0; right: 0; top: 120px;
    display: flex; justify-content: center; align-items: center; gap: 14px;
  }
  .back-brand-mark { width: 30px; height: 30px; background: var(--silver); }
  .back-brand-name { font-size: 46px; font-weight: 700; line-height: 1; }
  .back-url {
    position: absolute;
    left: 0; right: 0; top: 281px;
    text-align: center;
    font-size: 15px;
    font-weight: 700;
    font-style: italic;
    letter-spacing: 3.2px;
  }
</style>
</head>
<body>
  <section class="card card-front">
    <div class="brand">
      <div class="brand-mark"></div>
      <div class="brand-divider"></div>
      <div>
        <div class="brand-name">Nordwell AG</div>
        <div class="brand-tagline">DIGITALE STRATEGIEN</div>
      </div>
    </div>
    <div class="person">
      <div class="person-name">Your name</div>
      <div class="person-title">Job Title</div>
      <p class="address">Suite 102 Street name<br>State, Zip 2034,Country</p>
      <ul class="contacts">
        <li><svg viewBox="0 0 16 16"><path d="M3 1l3 3-1.5 2c1 2 3 4 5 5L11.5 9.5l3 3-2 2.5C6 14 1.5 8 1 3z"/></svg>127 345 9876</li>
        <li><svg viewBox="0 0 16 16"><path d="M4 1h8v4H4zM1 6h14v6h-2V9H3v3H1zM4 10h8v5H4z"/></svg>345 345 9876</li>
        <li><svg viewBox="0 0 16 16"><path d="M1 3h14v10H1zM2 4l6 5 6-5v1L8 10 2 5z" fill-rule="evenodd"/></svg>info@yourname.com</li>
        <li><svg viewBox="0 0 16 16"><path d="M8 1a7 7 0 100 14A7 7 0 008 1zm0 1.2c.9 0 1.8 1.6 2.1 4H5.9C6.2 3.8 7.1 2.2 8 2.2zM2.3 7.2h2.5v1.6H2.3zm8.9 0h2.5v1.6h-2.5zM5.9 9.8h4.2c-.3 2.4-1.2 4-2.1 4s-1.8-1.6-2.1-4zM5.9 7.2h4.2v1.6H5.9z"/></svg>www.yourweb.com</li>
      </ul>
    </div>
  </section>

  <section class="card card-back">
    <div class="back-brand">
      <div class="back-brand-mark"></div>
      <div class="back-brand-name">Nordwell AG</div>
    </div>
    <div class="back-url">www.yourweb.com</div>
  </section>
</body>
</html>
```